Design the Business card for NetVaultic

Business card required for a professional Cyber Security business.
Company Logo and Icon has already been provided however I would like other options for the logo and icon to compare to. Alternatively, please refine/enhance the image of the logo.icon I have already provided.

If you are going to use the provided logo and icon, I was thinking that the company raised Logo on White background would serve well on the front of the card. See attached. AND, a large company raised stand-alone icon to appear on black background on the back of the card with tagline 'Cyber Risk Management, Governance and Consulting' or 'Cyber Security for your Business' See attached.
Alternatively, provide your own design for the logo and icon.

Target Market(s)

Enterprise, Government, Financial.

Contact Information for Business Card

Tavin Orloweth
Founder and CEO

Email Address
Mobile Number
Website URL
LinkedIn URL

Logo Text

NetVaultic - see attached example of logo

Font styles to use
Other font styles liked:
• Berlin Sans FB

Requirements
Must have
• Clean large and bold icon on the back with tagline.
• Horizontal alignment,
Nice to have
• Round edges.
• Raised Logo/Icon
Should not have
• An unprofessional look and feel.

```html
<!DOCTYPE html>
<html lang="en">
<head>
<meta charset="utf-8">
<title>NetVaultic Business Card</title>
<link rel="stylesheet" href="https://fonts.googleapis.com/css2?family=Ubuntu:wght@400;500;700&display=swap">
<style>
  :root {
    --backdrop: #1c1c1d;
    --card-white: #f3f3f3;
    --card-black: #19191a;
    --brand-blue: #0a6bb8;
    --mark-blue: #4468c0;
    --brand-gold: #f2b705;
    --ink-white: #ffffff;
  }
  html, body {
    margin: 0;
    padding: 0;
    width: 1200px;
    height: 960px;
    overflow: hidden;
    background: var(--backdrop);
    font-family: "Ubuntu", sans-serif;
  }
  .canvas {
    position: relative;
    width: 1200px;
    height: 960px;
  }
  .card {
    position: absolute;
    width: 600px;
    height: 342px;
    box-shadow: 0 3px 8px rgba(0,0,0,0.6);
    overflow: hidden;
  }
  .card-front {
    left: 314px;
    top: 113px;
    background: var(--card-white);
  }
  .card-back {
    left: 311px;
    top: 472px;
    width: 601px;
    background: var(--card-black);
  }
  .front-band {
    position: absolute;
    left: 0;
    top: 0;
  }
  .front-brand {
    position: absolute;
    left: 0;
    right: 0;
    top: 100px;
    text-align: center;
    font-weight: 500;
    font-size: 44px;
    color: var(--brand-blue);
    letter-spacing: 0.5px;
  }
  .holder {
    position: absolute;
    left: 0;
    right: 0;
    top: 234px;
    text-align: center;
    white-space: nowrap;
  }
  .holder-name {
    color: var(--brand-gold);
    font-size: 21px;
    font-weight: 500;
  }
  .holder-dash {
    color: var(--brand-gold);
    font-size: 21px;
    font-weight: 700;
    margin: 0 8px;
  }
  .holder-title {
    color: var(--ink-white);
    font-size: 15px;
    font-weight: 500;
  }
  .divider {
    position: absolute;
    left: 48px;
    width: 503px;
    top: 266px;
    height: 1px;
    background: rgba(255,255,255,0.85);
  }
  .contacts {
    position: absolute;
    left: 0;
    right: 0;
    top: 276px;
    display: flex;
    justify-content: center;
    align-items: center;
    gap: 4px;
    color: var(--ink-white);
    font-size: 13.5px;
    font-weight: 500;
    white-space: nowrap;
  }
  .contact-item {
    display: inline-flex;
    align-items: center;
    gap: 4px;
  }
  .contact-icon {
    width: 13px;
    height: 13px;
    flex: none;
  }
  .back-brand {
    position: absolute;
    left: 124px;
    top: 112px;
    display: flex;
    align-items: center;
    gap: 12px;
  }
  .back-brand-dot {
    width: 80px;
    height: 80px;
    border-radius: 50%;
    background: var(--mark-blue);
  }
  .back-brand-name {
    font-size: 48px;
    font-weight: 500;
    color: var(--brand-blue);
  }
  .tagline {
    position: absolute;
    left: 0;
    right: 0;
    top: 276px;
    text-align: center;
    font-size: 17px;
    font-weight: 500;
  }
  .tagline-lead { color: var(--mark-blue); }
  .tagline-tail { color: var(--brand-gold); }
</style>
</head>
<body>
<main class="canvas">
  <section class="card card-front" aria-label="Card front">
    <svg class="front-band" width="600" height="342" viewBox="0 0 600 342" aria-hidden="true">
      <path d="M0,188 Q300,248 600,188 L600,326 Q300,280 0,342 Z" fill="var(--brand-blue)"/>
    </svg>
    <div class="front-brand">NetVaultic</div>
    <div class="holder">
      <span class="holder-name">Tavin Orloweth</span><span class="holder-dash">-</span><span class="holder-title">Founder &amp; CEO</span>
    </div>
    <div class="divider"></div>
    <div class="contacts">
      <span class="contact-item">
        <svg class="contact-icon" viewBox="0 0 13 13" aria-hidden="true"><rect x="3" y="0.5" width="7" height="12" rx="1.2" fill="none" stroke="var(--brand-gold)" stroke-width="1.6"/></svg>
        555 201 4386
      </span>
      <span class="contact-item">
        <svg class="contact-icon" viewBox="0 0 13 13" aria-hidden="true"><rect x="0.5" y="2.5" width="12" height="8" fill="var(--brand-gold)"/><path d="M0.5,2.5 L6.5,7 L12.5,2.5" fill="none" stroke="var(--brand-blue)" stroke-width="1"/></svg>
        tavin@netvaultic.com
      </span>
      <span class="contact-item">
        <svg class="contact-icon" viewBox="0 0 13 13" aria-hidden="true"><circle cx="6.5" cy="6.5" r="6" fill="var(--brand-gold)"/><ellipse cx="6.5" cy="6.5" rx="2.6" ry="6" fill="none" stroke="var(--brand-blue)" stroke-width="0.9"/><line x1="0.5" y1="6.5" x2="12.5" y2="6.5" stroke="var(--brand-blue)" stroke-width="0.9"/></svg>
        www.netvaultic.com
      </span>
      <span class="contact-item">
        <svg class="contact-icon" viewBox="0 0 13 13" aria-hidden="true"><circle cx="6.5" cy="6.5" r="6" fill="var(--brand-gold)"/></svg>
        netvaultic
      </span>
    </div>
  </section>

  <section class="card card-back" aria-label="Card back">
    <div class="back-brand">
      <div class="back-brand-dot"></div>
      <span class="back-brand-name">NetVaultic</span>
    </div>
    <p class="tagline"><span class="tagline-lead">Cyber Risk Management, </span><span class="tagline-tail">Governance &amp; Consulting</span></p>
  </section>
</main>
</body>
</html>
```